corvale institute of business and technology web site

I need web site for the institute which focus on business courses and computer course it is also for vocation train for employment It is also carear development and advancement .It should have links to online study resource which free
Industry/Entity Type
Business
Number of Pages Required
1 page
Look and feel
Each slider illustrates characteristics of the customer's brand and the style your logo design should communicate.

```html
<!DOCTYPE html>
<html lang="en">
<head>
<meta charset="utf-8">
<title>Corvale Institute of Business and Technology</title>
<link href="https://fonts.googleapis.com/css2?family=Open+Sans:ital,wght@0,400;0,600;0,700;0,800;1,400&family=Oswald:wght@500;700&display=swap" rel="stylesheet">
<style>
:root{
  --blue:#1f6fc1;
  --blue-dark:#16569c;
  --navy:#0f3f75;
  --ink:#2c3440;
  --text:#5d6670;
  --muted:#8b949d;
  --line:#d9dee3;
  --card:#d8e0e7;
  --panel:#eef1f4;
  --green:#7bb53a;
  --amber:#f2a51a;
  --footer:#4c5663;
  --footer-dark:#3f4853;
  --white:#ffffff;
}
*{box-sizing:border-box;margin:0;padding:0}
html,body{width:1200px;height:3100px;overflow:hidden}
body{font-family:"Open Sans",Arial,sans-serif;color:var(--text);background:var(--white);font-size:14px;line-height:1.55}
.wrap{width:1120px;margin:0 auto;position:relative}
h2.section-title{font-family:"Open Sans",Arial,sans-serif;font-weight:800;font-size:18px;color:var(--ink);text-transform:uppercase}

/* header */
.site-header{height:150px;position:relative}
.brand{position:absolute;left:40px;top:14px;display:flex;align-items:center;gap:12px}
.brand-mark{width:62px;height:62px;background:var(--blue);border-radius:6px}
.brand-name{font-weight:800;font-size:34px;color:var(--blue);line-height:1}
.brand-sub{font-weight:700;font-size:11px;color:var(--blue);letter-spacing:.5px;margin-top:4px}
.topbar{position:absolute;right:40px;top:10px;display:flex;gap:26px;align-items:flex-start}
.contact-item{font-size:12px;color:var(--ink)}
.contact-item b{display:flex;align-items:center;gap:6px;font-size:12px;font-weight:700;color:var(--ink)}
.contact-item span{display:block;margin-top:6px;font-weight:600}
.socials{display:flex;gap:5px}
.socials i{width:22px;height:22px;border-radius:50%;background:#5b6570;display:block}
.search{margin-top:8px;width:150px;height:26px;border:1px solid var(--line);font-size:11px;color:var(--muted);padding:4px 8px;display:flex;justify-content:space-between}
.main-nav{position:absolute;right:40px;top:120px;display:flex}
.main-nav a{font-size:13px;font-weight:700;color:var(--ink);text-decoration:none;padding:6px 14px;border-left:1px solid var(--line)}
.main-nav a:first-child{border-left:0}
.main-nav a.active{color:var(--blue)}

/* hero */
.hero{height:350px;position:relative;background:linear-gradient(100deg,#f09433 0%,#f6b55a 30%,#f8d6a2 48%,#3d8ed8 62%,#1d5ea8 100%)}
.hero .arrow{position:absolute;top:155px;width:34px;height:40px;background:rgba(20,30,45,.75)}
.hero .arrow.prev{left:0}.hero .arrow.next{right:0}
.dots{position:absolute;bottom:14px;left:50%;transform:translateX(-50%);display:flex;gap:6px}
.dots i{width:9px;height:9px;border-radius:50%;background:rgba(255,255,255,.6)}
.dots i.on{background:var(--white)}

/* welcome */
.welcome{margin-top:50px;height:260px;display:flex;justify-content:space-between}
.welcome-copy{width:700px}
.welcome-copy .kicker{font-weight:800;font-size:18px;color:var(--blue)}
.welcome-copy h1{font-weight:800;font-size:18px;color:var(--blue);margin-bottom:10px}
.welcome-copy p{font-size:12.5px;line-height:1.7}
.featured{width:310px}
.featured h3{font-weight:800;font-size:16px;color:var(--ink);border:1px solid var(--line);padding:8px 10px}
.video{height:160px;margin-top:10px;background:linear-gradient(135deg,#b9c9d6,#7f97ab 60%,#5c7387);position:relative}
.play{position:absolute;left:50%;top:50%;transform:translate(-50%,-50%)}
.featured p{font-size:12px;margin-top:6px}

/* programs */
.programs{margin-top:40px}
.programs-head{display:flex;justify-content:space-between;align-items:center;border-bottom:2px solid var(--line);padding-bottom:8px}
.cards{display:flex;gap:20px;margin-top:20px}
.card{width:265px;height:410px;background:var(--card);padding:12px;position:relative;overflow:hidden}
.card h4{font-size:13px;font-weight:700;color:var(--ink);height:40px;line-height:1.4}
.card .thumb{height:160px;margin:6px 0 10px}
.card p{font-size:12px;line-height:1.65}
.card .corner{position:absolute;right:0;bottom:0;width:0;height:0;border-left:30px solid transparent;border-bottom:30px solid var(--blue)}

/* banner */
.banner{margin-top:50px;height:510px;position:relative;background:linear-gradient(180deg,#e9ecef 0%,#d7dadd 55%,#b98a5e 56%,#8e6340 100%)}
.banner-text{position:absolute;left:110px;top:190px}
.banner-text .big{font-family:"Oswald",Impact,sans-serif;font-weight:700;font-size:62px;color:#2d2d2d;line-height:1}
.banner-text .small{font-family:"Oswald",Impact,sans-serif;font-weight:500;font-size:33px;color:#2d2d2d;letter-spacing:1px}
.btn-click{display:inline-block;margin-top:12px;background:var(--amber);color:var(--white);font-weight:800;font-size:20px;padding:8px 30px;border-radius:4px}

/* lower */
.lower{margin-top:60px;display:flex;justify-content:space-between;height:620px}
.lower-left{width:580px}
.testimonial{text-align:center;padding-top:10px}
.quote-icon{margin:18px auto 14px;width:58px;height:58px;border-radius:50%;background:var(--blue);display:flex;align-items:center;justify-content:center}
.testimonial blockquote{font-style:italic;font-size:13px;line-height:1.7;padding:0 30px}
.author{display:flex;justify-content:center;align-items:center;gap:10px;margin-top:16px;text-align:left}
.avatar{width:38px;height:38px;border-radius:50%;background:#c9b4a4}
.author b{display:block;font-size:12px;color:var(--ink)}
.author span{font-size:11px}
.alerts{margin-top:70px;background:var(--panel);padding:24px;text-align:center}
.alerts h3{font-weight:800;font-size:20px;color:var(--blue)}
.alerts p{font-size:12px}
.subscribe{display:flex;justify-content:center;margin-top:12px}
.subscribe span{width:300px;height:34px;border:1px solid var(--line);background:var(--white);font-size:12px;color:var(--muted);text-align:left;padding:7px 10px}
.subscribe b{background:var(--blue);color:var(--white);font-size:12px;padding:8px 16px}
.ask{width:410px;background:var(--blue)}
.ask h3{background:var(--blue-dark);color:var(--white);text-align:center;font-weight:800;font-size:18px;padding:16px}
.ask form{padding:16px 22px}
.ask label{display:block;color:var(--white);font-size:12px;font-weight:700;margin:10px 0 4px}
.row{display:flex;gap:10px}
.field{background:var(--white);height:34px;font-size:12px;color:var(--muted);padding:7px 10px;flex:1}
.field.tall{height:110px}
.submit{margin-top:20px;background:var(--green);color:var(--white);text-align:center;font-weight:800;font-size:18px;padding:12px}

/* footer */
.site-footer{position:absolute;left:0;top:2590px;width:1200px;height:510px;background:var(--footer);color:#cdd3d9}
.foot-cols{display:flex;gap:30px;padding:40px 40px 0}
.foot-col{width:255px;font-size:12px;line-height:1.9}
.foot-col h4{color:var(--white);font-size:13px;font-weight:800;border-bottom:1px solid #66717e;padding-bottom:8px;margin-bottom:10px}
.foot-col .news{margin-bottom:8px;line-height:1.5}
.foot-col .news em{display:block;font-style:normal;color:#9aa4ae;font-size:11px}
.contact-line{display:flex;gap:8px;margin-bottom:10px;line-height:1.5}
.partner{position:absolute;left:40px;bottom:40px;display:flex;align-items:center;gap:14px}
.partner small{color:var(--white);font-weight:800;font-size:13px;line-height:1.3}
.partner-badge{background:#111;color:var(--white);font-weight:700;font-size:16px;padding:18px 16px;display:flex;align-items:center;gap:8px}
.partner-badge i{width:14px;height:14px;background:var(--white);display:block}
.foot-bottom{position:absolute;right:40px;bottom:30px;text-align:right;font-size:11px}
.foot-bottom .socials{justify-content:flex-end;margin-bottom:10px}
.foot-bottom .socials i{background:#6c7784}
</style>
</head>
<body>

<header class="site-header">
  <div class="brand">
    <div class="brand-mark"></div>
    <div>
      <div class="brand-name">CORVALE</div>
      <div class="brand-sub">INSTITUTE OF BUSINESS &amp; TECHNOLOGY</div>
    </div>
  </div>
  <div class="topbar">
    <div class="contact-item">
      <b><svg width="14" height="14" viewBox="0 0 24 24"><path fill="#1f6fc1" d="M6.6 10.8a15 15 0 0 0 6.6 6.6l2.2-2.2c.3-.3.7-.4 1-.2 1.1.4 2.3.6 3.6.6.6 0 1 .4 1 1V20c0 .6-.4 1-1 1A17 17 0 0 1 3 4c0-.6.4-1 1-1h3.5c.6 0 1 .4 1 1 0 1.3.2 2.5.6 3.6.1.3 0 .7-.2 1z"/></svg>CALL US</b>
      <span>+260 211 555 014</span>
    </div>
    <div class="contact-item">
      <b><svg width="15" height="12" viewBox="0 0 24 18"><rect x="1" y="1" width="22" height="16" rx="2" fill="#1f6fc1"/><path d="M2 2l10 8 10-8" stroke="#fff" stroke-width="2" fill="none"/></svg>EMAIL US</b>
      <span>info@corvaleinstitute.com</span>
    </div>
    <div>
      <div class="socials"><i></i><i></i><i></i><i></i><i></i></div>
      <div class="search"><span>Search</span><svg width="12" height="12" viewBox="0 0 24 24"><circle cx="10" cy="10" r="7" stroke="#8b949d" stroke-width="2.5" fill="none"/><path d="M15 15l6 6" stroke="#8b949d" stroke-width="2.5"/></svg></div>
    </div>
  </div>
  <nav class="main-nav">
    <a class="active" href="#">HOME</a><a href="#">ABOUT US</a><a href="#">COURSES</a><a href="#">CONTACT US</a>
  </nav>
</header>

<section class="hero" role="img" aria-label="Slider image: smartphone surrounded by floating app icons on an orange and blue background">
  <span class="arrow prev"><svg width="34" height="40" viewBox="0 0 34 40"><path d="M20 13l-7 7 7 7" stroke="#fff" stroke-width="3" fill="none"/></svg></span>
  <span class="arrow next"><svg width="34" height="40" viewBox="0 0 34 40"><path d="M14 13l7 7-7 7" stroke="#fff" stroke-width="3" fill="none"/></svg></span>
  <div class="dots"><i class="on"></i><i></i><i></i></div>
</section>

<div class="wrap">
  <section class="welcome">
    <div class="welcome-copy">
      <div class="kicker">WELCOME TO</div>
      <h1>CORVALE INSTITUTE OF BUSINESS AND TECHNOLOGY</h1>
      <p>Corvale Institute of Business and Technology (CIBT) is a fast growing Education &amp; Training Solution Provider, focusing on holistic knowledge and skills interventions that impact livelihoods. It is established on the core values of making a meaningful and measurable difference on career aspirations and goals through innovative learning and knowledge management interventions. CIBT prepares students not only for professional careers but also inculcates the importance of discipline and equips them physically, mentally, socially and spiritually. The Institution is licensed and registered under the National Skills Training Authority (NSTA).</p>
    </div>
    <aside class="featured">
      <h3>FEATURED VIDEO</h3>
      <div class="video" role="img" aria-label="Video still of a lecturer presenting to a class">
        <svg class="play" width="44" height="44" viewBox="0 0 44 44"><circle cx="22" cy="22" r="21" fill="#1f6fc1"/><path d="M17 13l14 9-14 9z" fill="#fff"/></svg>
      </div>
      <p>Lorem ipsum dolor sit amet, consectetur adipiscing elit.</p>
    </aside>
  </section>

  <section class="programs">
    <div class="programs-head">
      <h2 class="section-title">Programs Offered</h2>
      <svg width="40" height="14" viewBox="0 0 40 14"><path d="M8 2L3 7l5 5M32 2l5 5-5 5" stroke="#5d6670" stroke-width="2.5" fill="none"/></svg>
    </div>
    <div class="cards">
      <article class="card">
        <h4>University Education – Long Distance Learning</h4>
        <div class="thumb" role="img" aria-label="Graduates in caps and gowns" style="background:linear-gradient(135deg,#6e7f90,#2f3e4f)"></div>
        <p>Lorem ipsum dolor sit amet, consectetur adipiscing elit, sed do eiusmod tempor incididunt ut labore et dolore magna aliqua. Ut enim ad minim.</p>
        <span class="corner"></span>
      </article>
      <article class="card">
        <h4>Modular Soft Skills</h4>
        <div class="thumb" role="img" aria-label="Team working together at a desk" style="background:linear-gradient(135deg,#c9d2da,#8a9aa8)"></div>
        <p>Lorem ipsum dolor sit amet, consectetur adipiscing elit, sed do eiusmod tempor incididunt ut labore et dolore magna aliqua. Ut enim ad minim.</p>
        <span class="corner"></span>
      </article>
      <article class="card">
        <h4>Direct to Basics (D2B)</h4>
        <div class="thumb" role="img" aria-label="Colourful learning concept icons" style="background:linear-gradient(135deg,#3b8fd6,#f2b13b)"></div>
        <p>Lorem ipsum dolor sit amet, consectetur adipiscing elit, sed do eiusmod tempor incididunt ut labore et dolore magna aliqua. Ut enim ad minim.</p>
        <span class="corner"></span>
      </article>
      <article class="card">
        <h4>Brightpath</h4>
        <div class="thumb" role="img" aria-label="Professional in a business suit" style="background:linear-gradient(135deg,#e6e9ec,#a7b0b8)"></div>
        <p>Lorem ipsum dolor sit amet, consectetur adipiscing elit, sed do eiusmod tempor incididunt ut labore et dolore magna aliqua. Ut enim ad minim.</p>
        <span class="corner"></span>
      </article>
    </div>
  </section>
</div>

<section class="banner" role="img" aria-label="Desk with laptop, lamp and books in front of a wall">
  <div class="banner-text">
    <div class="big">ONLINE STUDY</div>
    <div class="small">RESOURCE WHICH FREE</div>
    <span class="btn-click">CLICK HERE</span>
  </div>
</section>

<div class="wrap">
  <section class="lower">
    <div class="lower-left">
      <div class="testimonial">
        <h2 class="section-title">What Our People Say</h2>
        <div class="quote-icon"><svg width="24" height="20" viewBox="0 0 24 20"><path d="M0 20V11C0 4 4 1 9 0l1 3C7 4 5 6 5 9h5v11zm14 0V11c0-7 4-10 9-11l1 3c-3 1-5 3-5 6h5v11z" fill="#fff"/></svg></div>
        <blockquote>“Lorem ipsum dolor sit amet, consectetur adipiscing elit, sed do eiusmod tempor incididunt ut labore et dolore magna aliqua. Ut enim ad minim veniam, quis nostrud exercitation ullamco laboris nisi ut aliquip ex ea commodo consequat.”</blockquote>
        <div class="author">
          <div class="avatar" role="img" aria-label="Portrait of the reviewer"></div>
          <div><b>Nora Ellis</b><span>Lorem ipsum</span></div>
        </div>
      </div>
      <div class="alerts">
        <h3>AUCTION ALERTS!</h3>
        <p>Sign up to receive email alerts about our upcoming auctions</p>
        <div class="subscribe"><span>Enter your email address</span><b>Subscribe</b></div>
      </div>
    </div>
    <div class="ask">
      <h3>DO YOU HAVE A QUESTION?</h3>
      <form>
        <label>Your Name*</label>
        <div class="row"><div class="field">First Name</div><div class="field">Last Name</div></div>
        <label>Email*</label>
        <div class="row"><div class="field">Your Email Address here</div></div>
        <label>Phone</label>
        <div class="row"><div class="field">Phone Number</div></div>
        <label>Comments*</label>
        <div class="row"><div class="field tall"></div></div>
        <div class="submit">SUBMIT</div>
      </form>
    </div>
  </section>
</div>

<footer class="site-footer">
  <div class="foot-cols">
    <div class="foot-col">
      <h4>NAVIGATION</h4>
      Home<br>About Us<br>Courses<br>Contact Us
    </div>
    <div class="foot-col">
      <h4>PROGRAMS OFFERED</h4>
      University Education – Long Distance Learning<br>Modular Soft Skills<br>Direct to Basics (D2B)<br>Brightpath<br>Brightpath Skills In The Talent Continuum<br>Business Hub Lab<br>Technology Capabilities
    </div>
    <div class="foot-col">
      <h4>RECENT NEWS</h4>
      <div class="news"><em>January 28, 2015</em>Lorem ipsum dolor sit amet, consectetur adipiscing elit</div>
      <div class="news"><em>January 28, 2015</em>Lorem ipsum dolor sit amet, consectetur adipiscing elit</div>
      <div class="news"><em>January 28, 2015</em>Lorem ipsum dolor sit amet, consectetur adipiscing elit</div>
    </div>
    <div class="foot-col">
      <h4>CONTACT INFO</h4>
      <div class="contact-line"><svg width="12" height="16" viewBox="0 0 12 16"><path d="M6 0a6 6 0 0 1 6 6c0 4-6 10-6 10S0 10 0 6a6 6 0 0 1 6-6z" fill="#cdd3d9"/><circle cx="6" cy="6" r="2" fill="#4c5663"/></svg><span>Plot 14 Cedar Park,<br>Northgate, Lusaka</span></div>
      <div class="contact-line"><svg width="12" height="12" viewBox="0 0 24 24"><path fill="#cdd3d9" d="M6.6 10.8a15 15 0 0 0 6.6 6.6l2.2-2.2c.3-.3.7-.4 1-.2 1.1.4 2.3.6 3.6.6.6 0 1 .4 1 1V20c0 .6-.4 1-1 1A17 17 0 0 1 3 4c0-.6.4-1 1-1h3.5c.6 0 1 .4 1 1 0 1.3.2 2.5.6 3.6.1.3 0 .7-.2 1z"/></svg><span>Phone<br>+260 211 555 014</span></div>
      <div class="contact-line"><svg width="12" height="12" viewBox="0 0 24 24"><rect x="5" y="1" width="14" height="22" rx="2" fill="#cdd3d9"/></svg><span>Mobile<br>+260 977 555 208</span></div>
      <div class="contact-line"><svg width="13" height="10" viewBox="0 0 24 18"><rect x="1" y="1" width="22" height="16" rx="2" fill="#cdd3d9"/><path d="M2 2l10 8 10-8" stroke="#4c5663" stroke-width="2" fill="none"/></svg><span>info@corvaleinstitute.com</span></div>
    </div>
  </div>
  <div class="partner">
    <small>IN CONJUNCTION<br>WITH BRIGHTPATH</small>
    <div class="partner-badge"><i></i>BRIGHTPATH</div>
  </div>
  <div class="foot-bottom">
    <div class="socials"><i></i><i></i><i></i><i></i></div>
    © 2015 Corvale Institute of Business and Technology. All Rights Reserved.
  </div>
</footer>

</body>
</html>
```